Suite Refresh Partners - Tabletop Display

We need a 5'x5' trade show display for a hotel renovation company named "Suite Refresh Partners." Suite Refresh Partners is the most complete authority on hotel renovation in the country, and we're the only 100% turn-key renovator in Colorado. With one phone call, we deliver an approved design, FF&E purchasing, logistics, construction, installation, and warranty administration. The design needs to convey professionalism. Our goal is to help our clients reduce costs and reduce stress while achieving the best results. The colors should align with the attached brochure for our Raleigh office.

Target Market(s)

Hotel owners and general managers

Industry/Entity Type

Design Agency

Colors
3277b5
85acd3
cfdeed

Requirements
Must have
• Our product is a blend of design and construction. I need to convey our services and attention to detail without seeming salesy, bold, or aggressive. The goal is to convey confidence and help to relax our potential client base.
Nice to have
• Possibly one or more photos of completed projects. Not sure if exterior, lobby, or guest room photos would be best. I can send files via dropbox if that's helpful.
Should not have
• I've included a photo of the old display at a trade show. I strongly dislike the yellow and red on the display. Please try to stick to the color palette of the attached brochure.

```html
<!DOCTYPE html>
<html lang="en">
<head>
<meta charset="UTF-8">
<title>Suite Refresh Partners – Tabletop Display</title>
<link rel="stylesheet" href="https://fonts.googleapis.com/css2?family=Questrial&family=Open+Sans:wght@400;700&family=Oswald:wght@300;400&display=swap">
<style>
  :root {
    --navy: #0f2133;
    --navy-soft: #1b2c3d;
    --blue: #1f63a3;
    --blue-bright: #3277b5;
    --blue-light: #85acd3;
    --blue-pale: #cfdeed;
    --white: #ffffff;
  }
  * { margin: 0; padding: 0; box-sizing: border-box; }
  html, body { width: 1200px; height: 1200px; overflow: hidden; background: var(--white); }
  .display { position: relative; width: 1200px; height: 1200px; background: var(--white); font-family: "Open Sans", sans-serif; }

  .headline-band {
    position: absolute; left: 0; top: 0; width: 1200px; height: 131px;
    background: var(--navy); color: var(--white);
    display: flex; align-items: center; justify-content: center;
    font-family: "Questrial", sans-serif; font-size: 52px; letter-spacing: 1px;
  }

  .photo { position: absolute; }
  .photo-lobby {
    left: 0; top: 149px; width: 641px; height: 513px;
    background: linear-gradient(135deg, #e6cf9e 0%, #b89364 40%, #6e5a48 70%, #a88b6c 100%);
  }
  .photo-patio {
    left: 696px; top: 680px; width: 504px; height: 267px;
    background: linear-gradient(180deg, #d9d4cc 0%, #b8aa98 45%, #8a7e72 75%, #c9c1b6 100%);
  }

  .brand {
    position: absolute; left: 662px; top: 138px; width: 538px; height: 241px;
    display: flex; align-items: center; justify-content: center; gap: 22px;
  }
  .brand-square { width: 46px; height: 46px; background: var(--blue); flex: none; }
  .brand-name {
    font-family: "Questrial", sans-serif; font-size: 44px; line-height: 1.1;
    color: var(--blue); font-weight: 400;
  }

  .promise {
    position: absolute; left: 659px; top: 386px; width: 541px; height: 276px;
    background: linear-gradient(135deg, #2a3846 0%, var(--navy-soft) 60%, #121d28 100%);
    color: var(--white); display: flex; flex-direction: column; justify-content: center;
    padding-left: 88px; font-size: 50px; line-height: 66px;
  }
  .promise b { font-weight: 700; }

  .services {
    position: absolute; left: 0; top: 680px; width: 680px; height: 267px;
    background: var(--blue); color: var(--white);
    display: grid; grid-template-columns: 232px 1fr; column-gap: 0;
    padding: 36px 0 0 44px;
    font-family: "Oswald", sans-serif; font-weight: 300; font-size: 37px;
  }
  .services ul { list-style: none; }
  .services li { display: flex; align-items: center; gap: 16px; height: 51px; }
  .tick { width: 20px; height: 20px; flex: none; }

  .call-band {
    position: absolute; left: 0; top: 965px; width: 1200px; height: 129px;
    background: var(--navy); color: var(--white);
  }
  .call-text { position: absolute; left: 46px; top: 22px; font-family: "Questrial", sans-serif; }
  .call-lead { font-size: 27px; letter-spacing: 1px; }
  .call-main { font-size: 50px; line-height: 58px; letter-spacing: 1px; }
  .phone {
    position: absolute; left: 572px; top: 17px; width: 577px; height: 94px;
    background: var(--blue); border: 2px solid var(--white); border-radius: 14px;
    display: flex; align-items: center; justify-content: center;
    font-size: 70px; font-weight: 700;
  }

  .website {
    position: absolute; left: 0; top: 1094px; width: 1200px; height: 106px;
    display: flex; align-items: center; justify-content: center;
    font-family: "Questrial", sans-serif; font-size: 46px; letter-spacing: 4px; color: var(--navy);
  }
  .website span { color: var(--blue); }
</style>
</head>
<body>
<main class="display">
  <header class="headline-band">WE WILL DO YOUR ENTIRE RENOVATION</header>

  <div class="photo photo-lobby" role="img" aria-label="Renovated hotel lobby with stone fireplace, lounge chairs, sofa and orb chandelier"></div>

  <div class="brand">
    <div class="brand-square"></div>
    <div class="brand-name">Suite Refresh<br>Partners</div>
  </div>

  <section class="promise">
    <p>LOWEST <b>COST</b></p>
    <p>LEAST <b>HASSLE</b></p>
    <p>BEST <b>RESULTS</b></p>
  </section>

  <section class="services">
    <ul>
      <li><svg class="tick" viewBox="0 0 20 20"><rect x="1" y="1" width="18" height="18" fill="none" stroke="#fff" stroke-width="2"/><path d="M5 10l4 4 7-9" fill="none" stroke="#fff" stroke-width="2.4"/></svg>Planning</li>
      <li><svg class="tick" viewBox="0 0 20 20"><rect x="1" y="1" width="18" height="18" fill="none" stroke="#fff" stroke-width="2"/><path d="M5 10l4 4 7-9" fill="none" stroke="#fff" stroke-width="2.4"/></svg>Design</li>
      <li><svg class="tick" viewBox="0 0 20 20"><rect x="1" y="1" width="18" height="18" fill="none" stroke="#fff" stroke-width="2"/><path d="M5 10l4 4 7-9" fill="none" stroke="#fff" stroke-width="2.4"/></svg>Specication</li>
      <li><svg class="tick" viewBox="0 0 20 20"><rect x="1" y="1" width="18" height="18" fill="none" stroke="#fff" stroke-width="2"/><path d="M5 10l4 4 7-9" fill="none" stroke="#fff" stroke-width="2.4"/></svg>FF&amp;E</li>
    </ul>
    <ul>
      <li><svg class="tick" viewBox="0 0 20 20"><rect x="1" y="1" width="18" height="18" fill="none" stroke="#fff" stroke-width="2"/><path d="M5 10l4 4 7-9" fill="none" stroke="#fff" stroke-width="2.4"/></svg>Logistics</li>
      <li><svg class="tick" viewBox="0 0 20 20"><rect x="1" y="1" width="18" height="18" fill="none" stroke="#fff" stroke-width="2"/><path d="M5 10l4 4 7-9" fill="none" stroke="#fff" stroke-width="2.4"/></svg>Construction</li>
      <li><svg class="tick" viewBox="0 0 20 20"><rect x="1" y="1" width="18" height="18" fill="none" stroke="#fff" stroke-width="2"/><path d="M5 10l4 4 7-9" fill="none" stroke="#fff" stroke-width="2.4"/></svg>Installation</li>
      <li><svg class="tick" viewBox="0 0 20 20"><rect x="1" y="1" width="18" height="18" fill="none" stroke="#fff" stroke-width="2"/><path d="M5 10l4 4 7-9" fill="none" stroke="#fff" stroke-width="2.4"/></svg>Warranty Administration</li>
    </ul>
  </section>

  <div class="photo photo-patio" role="img" aria-label="Hotel courtyard patio with stone fire pit and lounge seating at dusk"></div>

  <section class="call-band">
    <div class="call-text">
      <p class="call-lead">A COMPLETE RENOVATION WITH</p>
      <p class="call-main">JUST ONE CALL!</p>
    </div>
    <div class="phone">303-555-0142</div>
  </section>

  <footer class="website">www.<span>suiterefresh</span>partners.com</footer>
</main>
</body>
</html>
```